Corportate Power Point Template

We need a corporate PPT Design for our startup Big Data company.

Basically, our company will ingest, analyze and generate dynamic Dashboards with data consumed from different sources like Social Networks, Enterprise Legacy Systems such as e-Commerce, ERP, CRM and others.

Company is headquartered in Brazil, but will have a global presence.

Industry/Entity Type

It Company

```html
<!DOCTYPE html>
<html lang="en">
<head>
<meta charset="utf-8">
<title>Project Title Here</title>
<link rel="stylesheet" href="https://fonts.googleapis.com/css2?family=Saira+Semi+Condensed:wght@400;500;600&display=swap">
<style>
  :root {
    --orange: #ff5a00;
    --orange-soft: #f57a2e;
    --ink: #3a3a3a;
    --body-ink: #333333;
    --placeholder: #e6e6e6;
    --placeholder-text: #bdbdbd;
    --rule: #dcdcdc;
    --paper: #ffffff;
  }
  * { box-sizing: border-box; margin: 0; padding: 0; }
  html, body { width: 1200px; height: 900px; overflow: hidden; background: var(--paper); }
  .slide {
    position: relative;
    width: 1200px;
    height: 900px;
    overflow: hidden;
    font-family: "Saira Semi Condensed", "Arial Narrow", sans-serif;
    background:
      radial-gradient(ellipse 620px 420px at 160px 160px, rgba(255,170,110,0.22), rgba(255,200,160,0.08) 60%, rgba(255,255,255,0) 100%),
      radial-gradient(ellipse 520px 380px at 1100px 120px, rgba(230,225,222,0.35), rgba(255,255,255,0) 100%),
      linear-gradient(180deg, #fffaf6 0%, #ffffff 70%);
  }
  .accent-bar {
    position: absolute; left: 0; top: 36px;
    width: 12px; height: 72px;
    background: var(--orange);
  }
  .slide-title {
    position: absolute; left: 34px; top: 28px;
    font-size: 56px; font-weight: 600; letter-spacing: 0.5px;
    color: var(--ink); line-height: 1.2;
  }
  .slide-title .highlight { color: var(--orange-soft); }

  .column { position: absolute; top: 165px; width: 326px; }
  .column--one { left: 51px; }
  .column--two { left: 424px; }
  .column--three { left: 807px; }

  .image-slot {
    margin-left: 4px;
    width: 320px; height: 242px;
    border-radius: 6px;
    background: var(--placeholder);
    display: flex; align-items: center; justify-content: center;
    color: var(--placeholder-text);
    font-size: 20px; font-weight: 500; letter-spacing: 0.3px;
  }
  .column-heading {
    margin-top: 19px;
    height: 48px;
    background: var(--orange);
    color: #fff;
    font-size: 28px; font-weight: 500;
    line-height: 48px;
    padding-left: 14px;
  }
  .column-text {
    margin-top: 12px;
    color: var(--body-ink);
    font-size: 20px; font-weight: 500;
    line-height: 28.5px;
    text-align: justify;
    padding-right: 2px;
  }
  .column-text + .column-text { margin-top: 28.5px; }

  .footer-rule {
    position: absolute; left: 0; top: 817px;
    width: 1200px; height: 2px; background: var(--rule);
  }
  .presenter {
    position: absolute; left: 12px; top: 850px;
    font-size: 20px; font-weight: 400; color: #222;
  }
  .presenter .presenter-name { color: var(--orange); }
  .brand {
    position: absolute; right: 14px; top: 838px;
    display: flex; align-items: center; gap: 10px;
  }
  .brand-mark { width: 26px; height: 26px; background: var(--orange); }
  .brand-name {
    font-size: 38px; font-weight: 500; color: var(--orange);
    line-height: 1;
  }
</style>
</head>
<body>
  <main class="slide">
    <div class="accent-bar"></div>
    <h1 class="slide-title"><span class="highlight">Project</span> Title Here</h1>

    <section class="column column--one">
      <div class="image-slot">IMAGE HERE</div>
      <h2 class="column-heading">Text Title Here</h2>
      <p class="column-text">Lorem ipsum dolor sit Lorem ipsum dolor sit Lorem ipsum dolor sit Lorem ipsum dolor sit Lorem ipsum dolor sit Lorem ipsum dolor sit Lorem ipsum dolor sit.</p>
      <p class="column-text">Lorem ipsum dolor sit Lorem ipsum dolor sit Lorem ipsum dolor sit Lorem ipsum</p>
    </section>

    <section class="column column--two">
      <div class="image-slot">IMAGE HERE</div>
      <h2 class="column-heading">Text Title Here</h2>
      <p class="column-text">Lorem ipsum dolor sit Lorem ipsum dolor sit Lorem ipsum dolor sit Lorem ipsum dolor sit Lorem ipsum dolor sit Lorem ipsum dolor sit Lorem ipsum dolor sit.</p>
      <p class="column-text">Lorem ipsum dolor sit Lorem ipsum dolor sit Lorem ipsum dolor sit Lorem ipsum</p>
    </section>

    <section class="column column--three">
      <div class="image-slot">IMAGE HERE</div>
      <h2 class="column-heading">Text Title Here</h2>
      <p class="column-text">Lorem ipsum dolor sit Lorem ipsum dolor sit Lorem ipsum dolor sit Lorem ipsum dolor sit Lorem ipsum dolor sit Lorem ipsum dolor sit Lorem ipsum dolor sit.</p>
      <p class="column-text">Lorem ipsum dolor sit Lorem ipsum dolor sit Lorem ipsum dolor sit Lorem ipsum</p>
    </section>

    <div class="footer-rule"></div>
    <p class="presenter">Persentatator Name : <span class="presenter-name">Marcelo Duarte</span></p>
    <div class="brand">
      <span class="brand-mark"></span>
      <span class="brand-name">Vantora Labs</span>
    </div>
  </main>
</body>
</html>
```